Business Card Design for Training Business

Clear Path Coaching is a new business that delivers training and other services with a focus on topics related to mental health and wellbeing, for example, Wellmind Response Course, Resilience etc. We have a strong focus on evidence-based psychology and neuroscience. I have a logo which I will upload with the brief, so please consider colours that work well with the logo.
Target Market(s)
Adults, workplaces (particularly government and not-for-profits)
Industry/Entity Type
Business
Contact Information for Business Card
Head Strong TrainingSamantha SellwoodDirector0438 770 850sam@headstrongtraining.com.auwww.headstrongtraining.com.au

```html
<!DOCTYPE html>
<html lang="en">
<head>
<meta charset="utf-8">
<title>Clear Path Coaching – Business Card</title>
<link href="https://fonts.googleapis.com/css2?family=Arimo:wght@400;700&display=swap" rel="stylesheet">
<style>
  :root {
    --backdrop: #e6e4e0;
    --card: #0c0c0c;
    --card-edge: #1a1a1a;
    --teal: #5ec4be;
    --white: #f4f4f4;
    --soft-grey: #b9b9b9;
    --rule: #d8d8d8;
  }
  * { margin: 0; padding: 0; box-sizing: border-box; }
  html, body {
    width: 1200px;
    height: 892px;
    overflow: hidden;
    background: var(--backdrop);
  }
  .canvas {
    width: 1200px;
    height: 892px;
    display: flex;
    align-items: center;
    justify-content: center;
  }
  .business-card {
    width: 900px;
    height: 514px;
    background: linear-gradient(160deg, var(--card-edge) 0%, var(--card) 55%);
    border-radius: 6px;
    box-shadow: 0 14px 40px rgba(0,0,0,0.25);
    position: relative;
    font-family: "Arimo", Arial, sans-serif;
    color: var(--white);
    text-align: center;
  }
  .brand {
    position: absolute;
    top: 42px;
    left: 0;
    right: 0;
    display: flex;
    flex-direction: column;
    align-items: center;
  }
  .brand-mark {
    width: 72px;
    height: 72px;
  }
  .brand-name {
    margin-top: 14px;
    font-weight: 400;
    font-size: 28px;
    letter-spacing: 5px;
    text-transform: uppercase;
    color: var(--soft-grey);
  }
  .divider {
    position: absolute;
    top: 184px;
    left: 136px;
    width: 628px;
    height: 2px;
    background: var(--rule);
  }
  .person {
    position: absolute;
    top: 216px;
    left: 0;
    right: 0;
  }
  .person-name {
    font-weight: 700;
    font-size: 28px;
    color: var(--teal);
    letter-spacing: 0.3px;
  }
  .person-role {
    margin-top: 6px;
    font-weight: 700;
    font-size: 18px;
    color: var(--white);
  }
  .contact {
    position: absolute;
    top: 306px;
    left: 0;
    right: 0;
    list-style: none;
    font-weight: 400;
    font-size: 24px;
    line-height: 44px;
    color: var(--white);
  }
</style>
</head>
<body>
  <main class="canvas">
    <article class="business-card">
      <header class="brand">
        <svg class="brand-mark" viewBox="0 0 72 72" aria-hidden="true">
          <circle cx="36" cy="36" r="33" fill="none" stroke="var(--teal)" stroke-width="3"/>
        </svg>
        <div class="brand-name">Clear Path Coaching</div>
      </header>
      <div class="divider"></div>
      <section class="person">
        <div class="person-name">Rebecca Tanfield</div>
        <div class="person-role">Director</div>
      </section>
      <ul class="contact">
        <li class="contact-phone">0491 362 517</li>
        <li class="contact-email">bec@clearpathcoaching.example.au</li>
        <li class="contact-web">www.clearpathcoaching.example.au</li>
      </ul>
    </article>
  </main>
</body>
</html>
```